TA BRAMLEY BUSINESS CARD DESIGN PROJECT

We need to utilize our logo that was expertly created on PixelHarbor and now need to match this with a business card design.

```html
<!DOCTYPE html>
<html lang="en">
<head>
<meta charset="utf-8">
<title>TA BRAMLEY Business Card</title>
<link rel="stylesheet" href="https://fonts.googleapis.com/css2?family=Open+Sans:wght@400;600;700&display=swap">
<style>
  :root {
    --canvas-bg: #232323;
    --card-front: #1c1c1d;
    --card-back: #1f1f24;
    --brand-blue: #1457b0;
    --text-light: #f2f2f2;
    --mark-dark: #0e0e10;
    --divider: #e8e8e8;
  }
  * { margin: 0; padding: 0; box-sizing: border-box; }
  html, body {
    width: 1200px; height: 780px; overflow: hidden;
    background: var(--canvas-bg);
    font-family: "Open Sans", Arial, sans-serif;
  }
  .canvas { position: relative; width: 1200px; height: 780px; }
  .card {
    position: absolute; top: 235px;
    width: 540px; height: 310px;
    overflow: hidden;
  }
  .card--front { left: 40px; background: var(--card-front); }
  .card--back { left: 620px; background: var(--card-back); }

  .accent-bar {
    position: absolute; width: 14px; height: 120px;
    background: var(--brand-blue);
  }
  .accent-bar--top { right: 0; top: 0; }
  .accent-bar--bottom { left: 0; bottom: 0; }

  .brand-name {
    position: absolute; left: 40px; top: 100px; width: 200px;
    color: var(--brand-blue);
    font-weight: 700; font-size: 30px; line-height: 1.1;
    letter-spacing: 2px; text-align: center;
  }
  .divider {
    position: absolute; left: 262px; top: 60px;
    width: 1px; height: 140px; background: var(--divider);
  }
  .contact { position: absolute; left: 290px; top: 52px; }
  .contact__name {
    color: var(--brand-blue); font-weight: 700; font-size: 22px; line-height: 1.1;
  }
  .contact__role {
    color: var(--text-light); font-size: 12px; margin-top: 3px;
  }
  .contact__list { list-style: none; margin-top: 18px; }
  .contact__item {
    display: flex; align-items: center; gap: 8px;
    color: var(--text-light); font-size: 12px; line-height: 20px;
  }
  .contact__icon { width: 12px; height: 12px; flex: none; }
  .address {
    position: absolute; left: 40px; right: 40px; bottom: 50px;
    color: var(--text-light); font-size: 13px; text-align: center;
  }

  .back-mark {
    position: absolute; inset: 0;
    display: flex; align-items: center; justify-content: center;
    color: var(--mark-dark);
    font-weight: 700; font-size: 52px; letter-spacing: 6px;
  }
</style>
</head>
<body>
<main class="canvas">
  <section class="card card--front">
    <span class="accent-bar accent-bar--top"></span>
    <span class="accent-bar accent-bar--bottom"></span>

    <div class="brand-name">TA BRAMLEY</div>
    <span class="divider"></span>

    <div class="contact">
      <p class="contact__name">Lena Markovic</p>
      <p class="contact__role">Managing Director</p>
      <ul class="contact__list">
        <li class="contact__item">
          <svg class="contact__icon" viewBox="0 0 12 12" aria-hidden="true"><path d="M2 1h2.5l1 3-1.5 1a6 6 0 0 0 3 3l1-1.5 3 1V10a1 1 0 0 1-1 1A9 9 0 0 1 1 2a1 1 0 0 1 1-1z" fill="#1457b0"/></svg>
          (555) 214-0387
        </li>
        <li class="contact__item">
          <svg class="contact__icon" viewBox="0 0 12 12" aria-hidden="true"><rect x="0.5" y="2" width="11" height="8" rx="1" fill="#1457b0"/><path d="M1 3l5 4 5-4" stroke="#1c1c1d" stroke-width="1" fill="none"/></svg>
          info@tabramley.com
        </li>
        <li class="contact__item">
          <svg class="contact__icon" viewBox="0 0 12 12" aria-hidden="true"><circle cx="6" cy="6" r="5.5" fill="#1457b0"/><path d="M0.5 6h11M6 0.5c-2.5 3-2.5 8 0 11M6 0.5c2.5 3 2.5 8 0 11" stroke="#1c1c1d" stroke-width="0.8" fill="none"/></svg>
          www.tabramley.com
        </li>
      </ul>
    </div>

    <p class="address">418 Harbor Crest Ave Lakeview, Ohio 44012 USA</p>
  </section>

  <section class="card card--back">
    <div class="back-mark">TA BRAMLEY</div>
  </section>
</main>
</body>
</html>
```